Hello my Name is Elias Moreno. I buy and sell vintage comic books, you can refer to my instragram page qpkz.comics to get ideas and inspiration. For the front of the card I would like my company logo QPKZ Comics with a yellow and black background with the bat signal or bat emblem like on my IG page and with my info Elias Moreno as the Owner and address/ phone number, PO Box 617283, Miami, FL 33827, 305-482-6170 and that I buy and sell comics & collectables . Also feel free to be open to other ideas if you want. Im not stuck on one design. For the back of the card I would like for it to say follow me on Instagram QPKZ.Comics with the ig emblem. Also would like the card to be vertical if possible. Thanks

```html
<!DOCTYPE html>
<html lang="en">
<head>
<meta charset="utf-8">
<title>QPKZ Comics – Business Card</title>
<link rel="stylesheet" href="https://fonts.googleapis.com/css2?family=PT+Sans:ital,wght@0,400;0,700;1,700&display=swap">
<style>
  :root {
    --stage: #1b1b1b;
    --card-yellow: #f9c513;
    --ink: #111111;
    --font-body: "PT Sans", Arial, sans-serif;
  }
  * { margin: 0; padding: 0; box-sizing: border-box; }
  html, body { width: 1200px; height: 900px; overflow: hidden; }
  body { background: var(--stage); position: relative; font-family: var(--font-body); color: var(--ink); }

  .card {
    position: absolute;
    top: 300px;
    width: 442px;
    height: 273px;
    border-radius: 10px;
    background: var(--card-yellow);
    overflow: hidden;
  }
  .card--front { left: 152px; }
  .card--back { left: 622px; }

  .card__pattern { position: absolute; inset: 0; background: var(--card-yellow); }

  .brand-name {
    position: absolute;
    font-weight: 700;
    font-size: 27px;
    line-height: 1;
    white-space: nowrap;
    color: var(--ink);
    transform: translate(-50%, -50%);
  }
  .card--front .brand-name { left: 139px; top: 128px; }
  .card--back .brand-name { left: 221px; top: 140px; font-size: 32px; }

  .contact { position: absolute; left: 237px; top: 68px; }
  .contact__name { font-size: 18px; font-weight: 700; letter-spacing: 0.2px; line-height: 1.1; }
  .contact__role { font-size: 14px; line-height: 1.2; margin-top: 2px; }
  .contact__phone { font-size: 14px; margin-top: 14px; display: flex; align-items: center; gap: 5px; }
  .contact__phone svg { width: 12px; height: 10px; }
  .contact__address { font-size: 14px; line-height: 18px; margin-top: 13px; }

  .tagline {
    position: absolute;
    left: 0; right: 0;
    top: 227px;
    text-align: center;
    font-size: 14px;
    font-weight: 700;
    font-style: italic;
    letter-spacing: -0.1px;
  }

  .follow {
    position: absolute;
    left: 0; right: 0;
    top: 232px;
    display: flex;
    justify-content: center;
    align-items: center;
    gap: 5px;
    font-size: 13px;
    font-weight: 700;
  }
  .follow__mark { width: 15px; height: 15px; background: var(--ink); }
</style>
</head>
<body>
  <section class="card card--front">
    <div class="card__pattern" role="img" aria-label="Repeating emblem pattern in darker yellow"></div>
    <div class="brand-name">QPKZ Comics</div>
    <div class="contact">
      <div class="contact__name">ELIAS MORENO</div>
      <div class="contact__role">OWNER</div>
      <div class="contact__phone">
        <svg viewBox="0 0 12 10" aria-hidden="true"><path d="M1 3.2C1 1.5 3.5 1 6 1s5 .5 5 2.2v.8H8.6V2.8H3.4V4H1z M2.5 9l1.3-4h4.4l1.3 4z" fill="#111"/></svg>
        <span>305-482-6170</span>
      </div>
      <div class="contact__address">PO Box 617283,<br>Miami, FL 33827</div>
    </div>
    <p class="tagline">WE BUY AND SELL COMICS &amp; COLLECTABLES</p>
  </section>

  <section class="card card--back">
    <div class="card__pattern" role="img" aria-label="Repeating emblem pattern in darker yellow"></div>
    <div class="brand-name">QPKZ Comics</div>
    <p class="follow"><span>Follow me on</span><span class="follow__mark"></span><span>QPKZ.Comics</span></p>
  </section>
</body>
</html>
```